Rig up a website for a Rigging Company

We already have a logo. Looking for a website design that works on pavlune.com.
Our rigging company uses semi trucks, forklifts, and similar equipment to move large machines.
Our logo is white, black and red.

Target Market(s)

Medical Industry (moving medical equipment), Utility Industry (power equipment), Food Industry (moving bottling/packing equipment), US Government (large equipment)

Industry/Entity Type

It Company

Coding

Coded - Design and coding required

Number of Pages Required

5+ page

Font styles to use
Sans Serif

Colors
ec1f27
ffffff
0355a3

Requirements
Must have
• Home page, About page, Services Page, and Contact Information page
Nice to have
• Pictures of semi and forklifts and ability to insert our own pictures of our equipment

```html
<!DOCTYPE html>
<html lang="en">
<head>
<meta charset="utf-8">
<title>Harlow Rigging</title>
<link href="https://fonts.googleapis.com/css2?family=Open+Sans:ital,wght@0,400;0,600;0,700;0,800;1,800&family=Lato:wght@400;700&display=swap" rel="stylesheet">
<style>
:root{
  --red:#ec1f27;
  --red-soft:#ee7b80;
  --ink:#111111;
  --grey:#8a8a8a;
  --ring:#c9c9c9;
  --icon:#8d8d8d;
  --card:#f2f1f1;
  --line:#dddddd;
  --white:#ffffff;
  --footer:#000000;
  --muted:#bdbdbd;
}
*{box-sizing:border-box;margin:0;padding:0}
html,body{width:1200px;height:2752px;overflow:hidden}
body{position:relative;background:var(--white);font-family:"Lato",Arial,sans-serif;color:var(--ink)}
a{color:inherit;text-decoration:none}

/* Header */
.site-header{position:absolute;top:0;left:0;width:1200px;height:95px;display:flex;align-items:center;justify-content:space-between;padding:0 86px}
.brand{display:flex;align-items:center;gap:10px;font-family:"Open Sans",Arial,sans-serif;font-weight:800;font-size:30px;color:var(--ink)}
.brand-mark{width:16px;height:16px;background:var(--red)}
.main-nav{display:flex;gap:33px;font-family:"Open Sans",Arial,sans-serif;font-weight:600;font-size:14px}
.main-nav .active{color:var(--red)}

/* Hero */
.hero{position:absolute;top:95px;left:0;width:1200px;height:443px;overflow:hidden}
.hero-photo{position:absolute;inset:0;background:linear-gradient(90deg,#3a2a2c 0%,#2a3444 25%,#4a4f58 50%,#2b3648 75%,#44282a 100%)}
.hero-shade{position:absolute;inset:0;background:rgba(10,12,18,.45)}
.hero-content{position:absolute;top:122px;left:0;width:100%;text-align:center;color:var(--white)}
.hero-title{font-family:"Open Sans",Arial,sans-serif;font-weight:700;font-size:48px;line-height:1.1}
.hero-title span{color:var(--red)}
.hero-text{width:730px;margin:12px auto 0;font-size:19px;line-height:1.6}
.btn{display:inline-block;font-family:"Lato",Arial,sans-serif;font-size:18px}
.hero .btn{margin-top:14px;width:146px;height:48px;line-height:48px;background:var(--white);color:var(--red)}
.slider-arrow{position:absolute;top:195px;width:28px;height:40px}
.slider-arrow.prev{left:30px}
.slider-arrow.next{right:30px}

/* Section headings */
.section-title{font-family:"Open Sans",Arial,sans-serif;font-style:italic;font-weight:800;font-size:36px;text-align:center}
.title-rule{width:216px;height:7px;margin:10px auto 0;border-top:2px solid var(--red-soft);border-bottom:2px solid var(--red-soft)}

/* Services */
.services{position:absolute;top:620px;left:0;width:1200px}
.service-list{position:relative;height:340px;margin-top:55px}
.service{position:absolute;top:0;width:260px;text-align:center}
.service svg{width:190px;height:190px}
.service-name{margin-top:32px;font-family:"Open Sans",Arial,sans-serif;font-weight:700;font-size:23px;color:var(--grey)}
.service.featured .service-name{color:var(--ink)}

/* About */
.about{position:absolute;top:1099px;left:0;width:1200px;height:485px;overflow:hidden;color:var(--white);text-align:center}
.about-photo{position:absolute;inset:0;background:radial-gradient(circle at 85% 55%,#5a1c1e 0%,#2a1a1b 25%,#1b1b1b 55%,#141414 100%)}
.about-content{position:relative;padding-top:60px}
.about .section-title{color:var(--white)}
.about-text{width:880px;margin:28px auto 0;font-size:13px;line-height:24px;color:#cfcfcf}
.about-text p+p{margin-top:22px}
.about .btn{margin-top:30px;width:154px;height:57px;line-height:57px;background:var(--red);color:var(--white)}

/* News */
.news{position:absolute;top:1640px;left:0;width:1200px}
.news-grid{position:relative;margin-top:30px;height:523px}
.news-card{position:absolute;top:0;width:320px;height:523px;background:var(--card)}
.news-photo{height:303px;border-bottom:5px solid var(--red)}
.news-body{padding:18px 18px 0}
.news-title{font-size:18px;font-weight:700}
.news-card.highlight .news-title,.news-card.highlight .read-more{color:var(--red)}
.news-date{margin-top:6px;font-size:11px;color:#666}
.news-rule{height:1px;background:var(--line);margin:12px -18px 0}
.news-text{margin-top:12px;font-size:12px;line-height:20px;color:#777}
.read-more{display:block;margin-top:14px;font-size:11px;color:#666}

/* Footer */
.site-footer{position:absolute;top:2336px;left:0;width:1200px;height:416px;background:var(--footer);color:var(--white)}
.footer-col{position:absolute;top:50px}
.footer-heading{font-size:18px;font-weight:400}
.contact-list{list-style:none;margin-top:24px;font-size:13px}
.contact-list li{display:flex;align-items:center;gap:22px;height:28px}
.contact-list svg{width:12px;height:12px}
.social{display:flex;gap:20px;margin-top:24px}
.social span{width:28px;height:28px;border-radius:50%;background:var(--white)}
.contact-form{display:flex;flex-direction:column;gap:14px;margin-top:22px;width:238px}
.field{border:1px solid #777;height:38px;padding:10px;font-size:12px;color:#999}
.field.message{height:62px}
.send{width:98px;height:26px;line-height:26px;background:var(--red);text-align:center;font-size:12px}
.newsletter-text{margin-top:20px;width:270px;font-size:11px;line-height:20px;color:var(--muted)}
.subscribe{display:flex;margin-top:26px;width:268px;height:47px}
.subscribe .email{flex:1;background:var(--white);color:#777;font-size:12px;padding:16px 20px}
.subscribe .go{width:56px;background:var(--red);display:flex;align-items:center;justify-content:center}
.footer-bottom{position:absolute;top:330px;left:0;width:100%;border-top:1px solid #222;height:86px;display:flex;align-items:center;justify-content:space-between;padding:0 86px;font-size:11px}
.footer-nav{display:flex;gap:30px}
</style>
</head>
<body>

<header class="site-header">
  <div class="brand"><span class="brand-mark"></span>Harlow Rigging</div>
  <nav class="main-nav">
    <a class="active" href="#">Home</a><a href="#">Services</a><a href="#">Products</a><a href="#">About</a><a href="#">News</a><a href="#">Resources</a><a href="#">Contact Us</a>
  </nav>
</header>

<section class="hero">
  <div class="hero-photo" role="img" aria-label="Forklift in a lane between stacked shipping containers"></div>
  <div class="hero-shade"></div>
  <svg class="slider-arrow prev" viewBox="0 0 28 40"><polyline points="22,4 6,20 22,36" fill="none" stroke="#fff" stroke-width="5"/></svg>
  <svg class="slider-arrow next" viewBox="0 0 28 40"><polyline points="6,4 22,20 6,36" fill="none" stroke="#fff" stroke-width="5"/></svg>
  <div class="hero-content">
    <h1 class="hero-title">Welcome to <span>Harlow Rigging</span></h1>
    <p class="hero-text">Sed ut perspiciatis unde omnis iste natus error sit voluptatem accusantium doloremque laudantium, totam rem aperiam, eaque ipsa quae ab</p>
    <a class="btn" href="#">Read More</a>
  </div>
</section>

<section class="services">
  <h2 class="section-title">Services We Provide</h2>
  <div class="title-rule"></div>
  <div class="service-list">
    <div class="service" style="left:74px">
      <svg viewBox="0 0 190 190"><circle cx="95" cy="95" r="90" fill="none" stroke="var(--ring)" stroke-width="7"/>
        <rect x="84" y="45" width="22" height="10" fill="var(--icon)"/><rect x="78" y="58" width="34" height="40" fill="var(--icon)"/>
        <path d="M95 100 v30 a14 14 0 1 1 -16 -8" fill="none" stroke="var(--icon)" stroke-width="8"/></svg>
      <div class="service-name">THE STANDARD</div>
    </div>
    <div class="service" style="left:336px">
      <svg viewBox="0 0 190 190"><circle cx="95" cy="95" r="90" fill="none" stroke="var(--ring)" stroke-width="7"/>
        <rect x="48" y="62" width="42" height="26" fill="var(--icon)"/><rect x="48" y="88" width="94" height="26" fill="var(--icon)"/>
        <rect x="100" y="76" width="40" height="10" fill="var(--icon)"/>
        <circle cx="68" cy="120" r="11" fill="var(--icon)"/><circle cx="124" cy="120" r="11" fill="var(--icon)"/></svg>
      <div class="service-name">LOREM IPSUM</div>
    </div>
    <div class="service featured" style="left:606px">
      <svg viewBox="0 0 190 190"><circle cx="95" cy="95" r="90" fill="none" stroke="var(--red-soft)" stroke-width="7"/>
        <rect x="110" y="40" width="6" height="80" fill="var(--red-soft)"/><rect x="118" y="62" width="28" height="28" fill="var(--red-soft)"/>
        <rect x="48" y="80" width="58" height="34" fill="var(--red-soft)"/><rect x="116" y="108" width="36" height="6" fill="var(--red-soft)"/>
        <circle cx="64" cy="120" r="11" fill="var(--red-soft)"/><circle cx="96" cy="120" r="11" fill="var(--red-soft)"/></svg>
      <div class="service-name">1914 TRANSLATION</div>
    </div>
    <div class="service" style="left:868px">
      <svg viewBox="0 0 190 190"><circle cx="95" cy="95" r="90" fill="none" stroke="var(--ring)" stroke-width="7"/>
        <rect x="58" y="48" width="74" height="84" rx="8" fill="var(--icon)"/><rect x="66" y="58" width="58" height="30" fill="#fff"/>
        <rect x="62" y="132" width="14" height="10" fill="var(--icon)"/><rect x="114" y="132" width="14" height="10" fill="var(--icon)"/></svg>
      <div class="service-name">IPSUM PASSAGE</div>
    </div>
  </div>
</section>

<section class="about">
  <div class="about-photo" role="img" aria-label="Dark textured backdrop with a large red crane hook on the right"></div>
  <div class="about-content">
    <h2 class="section-title">About Harlow Rigging</h2>
    <div class="title-rule"></div>
    <div class="about-text">
      <p>But I must explain to you how all this mistaken idea of denouncing pleasure and praising pain was born and I will give you a complete account of the system, and expound the actual teachings of the great explorer of the truth, the master-builder of human happiness. No one rejects, dislikes, or avoids pleasure itself, because it is pleasure, but because those who do not know how to pursue pleasure rationally encounter consequences that are extremely painful. Nor again is there anyone who loves or pursues or desires to obtain pain of itself, because it is pain, but because occasionally circumstances occur in which toil and pain can procure him some great pleasure.</p>
      <p>To take a trivial example, which of us ever undertakes laborious physical exercise, except to obtain some advantage from it? But who has any right to find fault with a man who chooses to enjoy a pleasure that has no annoying consequences, or one who avoids a pain that produces no resultant pleasure?</p>
    </div>
    <a class="btn" href="#">Read More</a>
  </div>
</section>

<section class="news">
  <h2 class="section-title">Latest News</h2>
  <div class="title-rule"></div>
  <div class="news-grid">
    <article class="news-card" style="left:86px">
      <div class="news-photo" role="img" aria-label="Yellow crane lifting a large machine crate under a blue sky" style="background:linear-gradient(160deg,#2f6fb8 0%,#7aa9d6 55%,#c9b27a 100%)"></div>
      <div class="news-body">
        <h3 class="news-title">1914 translation by J. Merrow</h3>
        <div class="news-date">March 20, 2017.</div>
        <div class="news-rule"></div>
        <p class="news-text">Sed ut perspiciatis unde omnis iste natus error sit voluptatem accusantium doloremque laudantium, totam rem aperiam, eaque ipsa quae ab illo inventore veritatis et quasi architecto beatae</p>
        <a class="read-more" href="#">Read More &gt;</a>
      </div>
    </article>
    <article class="news-card highlight" style="left:440px">
      <div class="news-photo" role="img" aria-label="Worker in red coveralls beside a red heavy-haul truck" style="background:linear-gradient(160deg,#5a6a78 0%,#8b2a2a 50%,#c23a32 100%)"></div>
      <div class="news-body">
        <h3 class="news-title">1914 translation by J. Merrow</h3>
        <div class="news-date">March 20, 2017.</div>
        <div class="news-rule"></div>
        <p class="news-text">Sed ut perspiciatis unde omnis iste natus error sit voluptatem accusantium doloremque laudantium, totam rem aperiam, eaque ipsa quae ab illo inventore veritatis et quasi architecto beatae</p>
        <a class="read-more" href="#">Read More &gt;</a>
      </div>
    </article>
    <article class="news-card" style="left:793px">
      <div class="news-photo" role="img" aria-label="Workers in hard hats walking past trucks under a port crane" style="background:linear-gradient(160deg,#b9b4a8 0%,#8e5a48 45%,#6f6a5c 100%)"></div>
      <div class="news-body">
        <h3 class="news-title">1914 translation by J. Merrow</h3>
        <div class="news-date">March 20, 2017.</div>
        <div class="news-rule"></div>
        <p class="news-text">Sed ut perspiciatis unde omnis iste natus error sit voluptatem accusantium doloremque laudantium, totam rem aperiam, eaque ipsa quae ab illo inventore veritatis et quasi architecto beatae</p>
        <a class="read-more" href="#">Read More &gt;</a>
      </div>
    </article>
  </div>
</section>

<footer class="site-footer">
  <div class="footer-col" style="left:86px">
    <h4 class="footer-heading">Contact Us</h4>
    <ul class="contact-list">
      <li><svg viewBox="0 0 12 12"><path d="M6 0a4 4 0 0 1 4 4c0 3-4 8-4 8S2 7 2 4a4 4 0 0 1 4-4z" fill="#fff"/><circle cx="6" cy="4" r="1.5" fill="#000"/></svg>2417 Fenwick Mill Road, Michigan, 48190.</li>
      <li><svg viewBox="0 0 12 12"><path d="M2 1l2 0 1 3-1.5 1a7 7 0 0 0 3.5 3.5L8 7l3 1 0 2c0 1-1 1.5-2 1.5A9 9 0 0 1 .5 3C.5 2 1 1 2 1z" fill="#fff"/></svg>555-208-3471</li>
      <li><svg viewBox="0 0 12 12"><rect x="0" y="2" width="12" height="8" fill="#fff"/><polyline points="0,2 6,7 12,2" fill="none" stroke="#000" stroke-width="1"/></svg>info@pavlune.com</li>
    </ul>
    <div class="social"><span></span><span></span><span></span></div>
  </div>
  <div class="footer-col" style="left:488px">
    <h4 class="footer-heading">Contact Form</h4>
    <div class="contact-form">
      <div class="field">Name</div>
      <div class="field">Email</div>
      <div class="field message">Message</div>
      <div class="send">SEND</div>
    </div>
  </div>
  <div class="footer-col" style="left:846px">
    <h4 class="footer-heading">Newsletter Subscribe</h4>
    <p class="newsletter-text">Subscribe to our newsletter and we will inform you about newest Projects.</p>
    <div class="subscribe">
      <div class="email">Your email</div>
      <div class="go"><svg width="22" height="22" viewBox="0 0 22 22"><path d="M21 1L1 9l7 3 2 8 3-6 8-13zM8 12l13-11" fill="none" stroke="#fff" stroke-width="2" stroke-linejoin="round"/></svg></div>
    </div>
  </div>
  <div class="footer-bottom">
    <nav class="footer-nav"><a href="#">Home</a><a href="#">Services</a><a href="#">Products</a><a href="#">About</a><a href="#">News</a><a href="#">Resources</a><a href="#">Contact Us</a></nav>
    <div>Copyright 2017 Harlow Rigging. All rights reserved.&nbsp;&nbsp;&nbsp;&nbsp;&nbsp;C24</div>
  </div>
</footer>

</body>
</html>
```